BrivoTerna. Lantern of the Steady Harvest. Business card

Professional business card for BrivoTerna (Lantern of the Steady Harvest)
My rationale: Strategy-> Execution-> Results-> Value that lead to the BrivoTerna name: We put the Lantern of the Steady Harvest.
We deliver value to our customers helping them at defining a good strategy (cyan arrow). 90% of well formulated strategies fail due to poor execution so we also consider strategical execution very important (green arrow). Due to the execution we obtain the results (blue arrow). Finally, the results provide feedback to redefine strategy, and the new strategy has to be executed and new results obtained providing new feedback and on and on. It's like a wheel that finally, must create corporate value: value for shareholders, staholders, employees, providers...-

Target Market(s)

CEOs and steering comitees , invewrnent funds

Industry/Entity Type

Business Consultant

Contact Information for Business Card

Teodoro Vinsquel
CEO & Founder
teodoro.vinsquel@brivoterna-example.com
Mobile: +34 655.803.912
www.brivoterna-example.com

Colors

Designer to choose colors to be used in the design.

Requirements
Nice to have
• Nice to hace the words: Strategy, execution, results
• Nice to vave the claim: Lantern of the Steady Harvest
• The three colors should be shown:
• cyan for STRATEGY
• green for EXECUTION
• blue for RESULTS
Should not have
• Complete black background

```html
<!DOCTYPE html>
<html lang="en">
<head>
<meta charset="utf-8">
<title>BrivoTerna — Business Card</title>
<link rel="stylesheet" href="https://fonts.googleapis.com/css2?family=Open+Sans:wght@400;600;700&display=swap">
<style>
  :root {
    --navy: #2a3181;
    --cyan: #2aa7dc;
    --green: #8dc33f;
    --paper: #f7f6f1;
    --ink: #333333;
    --stage: #dcdcdc;
  }
  * { margin: 0; padding: 0; box-sizing: border-box; }
  html, body { width: 1200px; height: 787px; overflow: hidden; }
  body {
    background: var(--stage);
    font-family: "Open Sans", Arial, sans-serif;
    display: flex;
    align-items: center;
    justify-content: center;
    gap: 50px;
  }
  .card {
    position: relative;
    width: 540px;
    height: 309px;
    overflow: hidden;
    box-shadow: 0 4px 14px rgba(0,0,0,0.18);
  }

  /* Back side */
  .card-back { background: var(--navy); }
  .card-back .brand {
    position: absolute;
    left: 0; right: 0; top: 108px;
    display: flex; align-items: center; justify-content: center; gap: 14px;
  }
  .brand-name {
    font-weight: 700;
    font-size: 52px;
    letter-spacing: -1px;
    line-height: 1;
  }
  .card-back .brand-name { color: var(--paper); }
  .brand-mark { width: 24px; height: 24px; }
  .card-back .brand-mark { background: var(--paper); }
  .back-band {
    position: absolute; left: 0; right: 0; bottom: 0; height: 30px;
    display: flex;
  }
  .back-band .seg-green { background: var(--green); }
  .back-band .seg-green.left { width: 90px; }
  .back-band .seg-green.right { flex: 1; }
  .back-band .tagline {
    width: 330px;
    background: var(--cyan);
    color: #fff;
    font-size: 12px;
    font-weight: 600;
    letter-spacing: 1px;
    text-transform: uppercase;
    display: flex; align-items: center; justify-content: center;
    border-top: 4px solid var(--cyan);
    height: 22px;
    align-self: flex-end;
  }
  .back-band .right { height: 30px; }

  /* Front side */
  .card-front { background: var(--paper); }
  .card-front .brand {
    position: absolute; left: 150px; top: 40px;
    display: flex; align-items: center; gap: 12px;
  }
  .card-front .brand-name { color: var(--navy); font-size: 40px; }
  .card-front .brand-mark { background: var(--navy); width: 18px; height: 18px; }
  .divider {
    position: absolute; left: 40px; right: 40px; top: 128px;
    height: 2px; background: var(--green);
  }
  .contact {
    position: absolute; left: 40px; top: 142px;
    list-style: none;
    font-size: 11.5px; color: var(--ink);
    line-height: 20px;
  }
  .contact li { display: flex; align-items: center; gap: 8px; }
  .contact svg { width: 12px; height: 12px; flex: none; }
  .person {
    position: absolute; right: 40px; top: 142px; text-align: right;
  }
  .person-name { font-size: 22px; font-weight: 700; color: var(--navy); line-height: 1.1; }
  .person-name .surname { color: var(--cyan); }
  .person-role { font-size: 13px; color: var(--ink); margin-top: 2px; }
  .pillars {
    position: absolute; right: 40px; bottom: 34px; text-align: right;
    list-style: none; font-size: 13px; font-weight: 700; line-height: 16px;
  }
  .pillar-strategy { color: var(--cyan); }
  .pillar-execution { color: var(--green); }
  .pillar-results { color: var(--navy); }
  .front-band {
    position: absolute; left: 0; right: 0; bottom: 0; height: 14px; display: flex;
  }
  .front-band .seg-navy { width: 110px; background: var(--navy); }
  .front-band .seg-green { width: 190px; background: var(--green); }
  .front-band .seg-cyan { flex: 1; background: var(--cyan); }
</style>
</head>
<body>

  <section class="card card-back" aria-label="Business card, back">
    <div class="brand">
      <span class="brand-name">BrivoTerna</span>
      <span class="brand-mark"></span>
    </div>
    <div class="back-band">
      <span class="seg-green left"></span>
      <span class="tagline">Lantern of the Steady Harvest</span>
      <span class="seg-green right"></span>
    </div>
  </section>

  <section class="card card-front" aria-label="Business card, front">
    <div class="brand">
      <span class="brand-name">BrivoTerna</span>
      <span class="brand-mark"></span>
    </div>
    <div class="divider"></div>

    <ul class="contact">
      <li>
        <svg viewBox="0 0 12 12"><rect x="3" y="0.5" width="6" height="11" rx="1" fill="none" stroke="#2a3181" stroke-width="1.2"/><rect x="5" y="9.3" width="2" height="1" fill="#2a3181"/></svg>
        +34 655.803.912
      </li>
      <li>
        <svg viewBox="0 0 12 12"><rect x="0.6" y="2.5" width="10.8" height="7.5" fill="none" stroke="#2a3181" stroke-width="1.2"/><path d="M0.6 2.5 L6 7 L11.4 2.5" fill="none" stroke="#2a3181" stroke-width="1.2"/></svg>
        teodoro.vinsquel@brivoterna-example.com
      </li>
      <li>
        <svg viewBox="0 0 12 12"><circle cx="6" cy="6" r="5.2" fill="none" stroke="#2a3181" stroke-width="1.1"/><ellipse cx="6" cy="6" rx="2.2" ry="5.2" fill="none" stroke="#2a3181" stroke-width="1"/><path d="M1 6 H11" stroke="#2a3181" stroke-width="1"/></svg>
        www.brivoterna-example.com
      </li>
    </ul>

    <div class="person">
      <p class="person-name">Teodoro <span class="surname">Vinsquel</span></p>
      <p class="person-role">CEO &amp; Founder</p>
    </div>

    <ul class="pillars">
      <li class="pillar-strategy">Strategy</li>
      <li class="pillar-execution">Execution</li>
      <li class="pillar-results">Results</li>
    </ul>

    <div class="front-band">
      <span class="seg-navy"></span>
      <span class="seg-green"></span>
      <span class="seg-cyan"></span>
    </div>
  </section>

</body>
</html>
```